Website Design for a Chemical Sales Company

We are working with a Chemical Sales Company in California. They sell various chemicals throughout the US.
Types of products they sell: https://www.wardenvale.example/us/products/all
https://www.molvista.example/products/kerrin/glacyn-glycol-thermal-fluids/glacyn-propylene-glycol-thermal-fluids
Some sites to use for inspiration:
https://www.molvista.example
https://www.kerrin.example/en-us
Thank you for taking the time to consider designing a website for us. We are web developers based in Stockton, CA, USA. Most of our projects go through the same process. Understanding this process may help you win a project with us. We custom-code all of our websites in-house. We don’t have any requirements as to what tools you use for your design, but we ask that you follow these guidelines.
IMAGES:
If you use any images or icons in the design, we ask that you have a link to the asset so we can purchase the image/icon. Most of the designs we submit do not have the customer’s images on them unless they have some great images. Be creative; show us the feeling you are trying to portray with your image choices. Use any royalty-free site you choose. We subscribe to Pelmora and mainly use their images, but we can purchase images outside of Pelmora. PLEASE NOTE: we will not submit designs to clients with watermarks on the images.
FONTS:
We ask that you identify the fonts you’re using in the design. This can be done in a message if you want. We typically use Google Fonts and Pelmora Fonts.
CONTENT:
We're always open to different content and ideas. We often submit designs with stock images so the client can see our vision. We typically take pictures after the website launch to use their images with our vision. Lorem Ipsum is fine for paragraphs, but we ask that you make the Headers with correct English. We want to be able to show the vision and identify the sections of the website.
INSPIRATION:
We typically add a couple of links in the brief of websites we like to help you get started in your design.
REVISIONS:
We do not often ask for revisions of the designs unless we see something in the design that may not appeal to the client. If there are slight changes that we want to make, we do that in the development process.
FEEDBACK:
We rarely give feedback on designs during the design process. We are working on many website projects and do not have the time to provide feedback. We usually respond if your request is well thought out and asks specific questions, but a note asking “feedback, please” usually goes unanswered.

```html
<!DOCTYPE html>
<html lang="en">
<head>
<meta charset="utf-8">
<title>Novabond — Chemical Sales</title>
<link rel="stylesheet" href="https://fonts.googleapis.com/css2?family=Poppins:wght@300;400;500;600&family=Lato:wght@400;700&family=Open+Sans:wght@700;800&display=swap">
<style>
:root{
  --blue:#0793d8;
  --ink:#111111;
  --text:#333333;
  --soft:#f3f3f3;
  --card-img:#f4f4f4;
  --gold:#f5a623;
  --footer:#000000;
  --white:#ffffff;
}
*{box-sizing:border-box;margin:0;padding:0}
html,body{width:1200px;height:2313px;overflow:hidden;background:var(--white)}
body{position:relative;font-family:"Lato",sans-serif;color:var(--text)}
.abs{position:absolute}

/* header */
.brand{left:111px;top:38px;display:flex;align-items:center;gap:8px;font-family:"Poppins",sans-serif;font-weight:300;font-size:27px;letter-spacing:1px;color:var(--ink)}
.brand .dot{width:14px;height:14px;border-radius:50%;background:var(--blue)}
.contact-top{top:41px;left:670px;display:flex;align-items:center;font-family:"Poppins",sans-serif;font-size:15.5px;color:var(--blue)}
.contact-top span{display:flex;align-items:center;gap:10px}
.contact-top .sep{width:1.5px;height:20px;background:var(--blue);margin:0 28px}

/* hero */
.hero{left:0;top:105px;width:1200px;height:552px;
  background:
    radial-gradient(ellipse 260px 200px at 720px 300px,rgba(200,214,228,.38),transparent 70%),
    radial-gradient(ellipse 200px 260px at 660px 200px,rgba(120,140,160,.35),transparent 70%),
    radial-gradient(ellipse 300px 200px at 160px 160px,rgba(90,120,150,.35),transparent 70%),
    linear-gradient(180deg,#27394c 0%,#1a2a3b 55%,#0f1c2b 100%)}
.hero-brand{left:0;top:105px;width:1200px;height:552px;display:flex;align-items:center;justify-content:center;gap:22px;padding-bottom:14px;font-family:"Poppins",sans-serif;font-weight:300;font-size:82px;letter-spacing:5px;color:var(--white)}
.hero-brand .dot{width:46px;height:46px;border-radius:50%;background:var(--white)}

/* nav */
.nav{left:111px;top:105px;width:978px;height:64px;background:var(--blue);border-radius:10px 10px 0 0;font-family:"Poppins",sans-serif;font-size:15px;color:var(--white)}
.nav a{position:absolute;top:21px;color:var(--white);text-decoration:none;white-space:nowrap}
.nav a.active{font-weight:600;border-bottom:2px solid var(--white);padding-bottom:1px}
.nav .search{position:absolute;right:21px;top:19px;width:26px;height:26px;border-radius:50%;background:var(--white);display:flex;align-items:center;justify-content:center}

/* headings */
.section-title{left:0;width:1200px;text-align:center;font-family:"Open Sans",sans-serif;font-weight:800;font-size:34px;color:var(--ink);letter-spacing:.5px}
.section-title em{font-style:normal;color:var(--blue)}
.intro{left:220px;top:762px;width:760px;text-align:center;font-size:15px;line-height:29px;color:var(--text)}

/* products */
.card{top:845px;width:295px;height:395px;background:var(--white);border-radius:14px;box-shadow:0 1px 10px rgba(0,0,0,.14)}
.card .photo{position:absolute;left:15px;top:19px;width:265px;height:275px;border-radius:12px;background:var(--card-img)}
.photo.filter{background:radial-gradient(ellipse 60px 95px at 50% 52%,#2a2a2a 0%,#3b3b3b 55%,rgba(244,244,244,0) 100%),var(--card-img)}
.photo.pump{background:radial-gradient(ellipse 62px 115px at 50% 50%,#e8391c 0%,#ee4a2a 60%,rgba(244,244,244,0) 100%),var(--card-img)}
.photo.kit{background:radial-gradient(ellipse 95px 72px at 52% 50%,#2f9a3e 0%,#2a62b8 62%,rgba(244,244,244,0) 100%),var(--card-img)}
.card h3{position:absolute;left:0;top:320px;width:100%;text-align:center;font-weight:700;font-size:17px;letter-spacing:.6px;color:var(--ink)}
.card .stars{position:absolute;left:0;top:349px;width:100%;text-align:center;font-size:18px;color:var(--gold);letter-spacing:1px}
.arrow{top:1026px;width:30px;height:30px;border-radius:50%;background:var(--ink);display:flex;align-items:center;justify-content:center}

/* testimonials */
.reviews{left:0;top:1329px;width:1200px;height:580px;background:var(--soft)}
.avatar{border-radius:50%}
.reviewer{left:0;width:1200px;text-align:center;font-family:"Poppins",sans-serif}
.quote-text{left:270px;top:1745px;width:660px;text-align:center;font-family:"Poppins",sans-serif;font-weight:500;font-size:15.5px;line-height:26px;color:#3a3a3a}
.dots{left:543px;top:1853px;display:flex;gap:8px}
.dots i{width:12px;height:12px;border-radius:50%;background:#c9dcf2}
.dots i.on{background:var(--blue)}

/* footer */
.footer{left:0;top:1909px;width:1200px;height:404px;background:var(--footer)}
.foot-brand{left:111px;top:2023px;display:flex;align-items:center;gap:8px;font-family:"Poppins",sans-serif;font-weight:300;font-size:31px;letter-spacing:1px;color:var(--white)}
.foot-brand .dot{width:16px;height:16px;border-radius:50%;background:var(--white)}
.social{top:2104px;width:32px;height:32px;border-radius:50%;background:var(--white)}
.col h4{font-family:"Poppins",sans-serif;font-weight:500;font-size:21px;color:var(--blue);margin-bottom:17px}
.col ul{list-style:none}
.col li{display:flex;align-items:center;gap:10px;height:34px;font-size:16px;color:var(--white)}
.col.quick li{font-weight:700}
.ct{display:flex;align-items:center;gap:13px;font-size:16px;color:var(--white);line-height:27px}
.ct .ic{width:32px;height:32px;border-radius:50%;background:var(--white);display:flex;align-items:center;justify-content:center;flex:none}
.rule{left:111px;top:2231px;width:978px;height:1px;background:#cfcfcf}
.copy{left:0;top:2266px;width:1200px;text-align:center;font-weight:700;font-size:16px;color:var(--white)}
</style>
</head>
<body>

<header>
  <div class="abs brand"><span>NOVABOND</span><span class="dot"></span></div>
  <div class="abs contact-top">
    <span><svg width="13" height="13" viewBox="0 0 24 24"><path fill="#0793d8" d="M6.6 10.8a15.1 15.1 0 0 0 6.6 6.6l2.2-2.2c.3-.3.7-.4 1-.2 1.1.4 2.3.6 3.6.6.6 0 1 .4 1 1V20c0 .6-.4 1-1 1A17 17 0 0 1 3 4c0-.6.4-1 1-1h3.5c.6 0 1 .4 1 1 0 1.3.2 2.5.6 3.6.1.3 0 .7-.2 1z"/></svg>+1 555 014 2387</span>
    <span class="sep"></span>
    <span><svg width="14" height="11" viewBox="0 0 24 18"><rect width="24" height="18" rx="2" fill="#0793d8"/><path d="M2 3l10 7 10-7" stroke="#fff" stroke-width="2" fill="none"/></svg>info@novabond.example</span>
  </div>
</header>

<section>
  <div class="abs hero" role="img" aria-label="Scientist in a white coat looking into a microscope in a dimly lit laboratory"></div>
  <div class="abs hero-brand"><span>NOVABOND</span><span class="dot"></span></div>
  <nav class="abs nav">
    <a class="active" style="left:24px">Home</a>
    <a style="left:130px">About</a>
    <a style="left:237px">Product</a>
    <a style="left:358px">Latest News</a>
    <a style="left:511px">Chemical sales</a>
    <a style="left:690px">Reviews</a>
    <a style="left:813px">Contact Us</a>
    <span class="search"><svg width="11" height="11" viewBox="0 0 24 24"><circle cx="10" cy="10" r="6.5" stroke="#111" stroke-width="3" fill="none"/><path d="M15 15l6 6" stroke="#111" stroke-width="3"/></svg></span>
  </nav>
</section>

<section>
  <h2 class="abs section-title" style="top:706px">OUR <em>PRODUCTS</em></h2>
  <p class="abs intro">Itaque earum rerum hic tenetur a sapiente delectus, ut aut reiciendis voluptatibus maiores alias consequatur aut perferendis doloribus asperiores repellat.</p>

  <div class="abs arrow" style="left:33px"><svg width="12" height="12" viewBox="0 0 24 24"><path d="M15 4l-8 8 8 8" stroke="#fff" stroke-width="3.5" fill="none"/></svg></div>
  <div class="abs arrow" style="left:1131px"><svg width="12" height="12" viewBox="0 0 24 24"><path d="M9 4l8 8-8 8" stroke="#fff" stroke-width="3.5" fill="none"/></svg></div>

  <article class="abs card" style="left:112px">
    <div class="photo filter" role="img" aria-label="Black magnetic system filter with brass valves"></div>
    <h3>CLARIFIER SPIRAL™</h3>
    <div class="stars">★★★★★</div>
  </article>
  <article class="abs card" style="left:454px">
    <div class="photo pump" role="img" aria-label="Red power flushing pump unit"></div>
    <h3>PURGELINE P90</h3>
    <div class="stars">★★★★★</div>
  </article>
  <article class="abs card" style="left:795px">
    <div class="photo kit" role="img" aria-label="Blue and green carry case test kit"></div>
    <h3>PURGELINE TEST KIT</h3>
    <div class="stars">★★★★★</div>
  </article>
</section>

<section>
  <div class="abs reviews"></div>
  <h2 class="abs section-title" style="top:1408px">WHAT <em>CUSTOMER SAYS</em></h2>

  <div class="abs avatar" style="left:127px;top:1566px;width:66px;height:66px;background:radial-gradient(circle at 50% 45%,#f2cdb2 0%,#d9a887 60%,#b88466 100%)" role="img" aria-label="Portrait of a customer"></div>
  <div class="abs avatar" style="left:1003px;top:1492px;width:48px;height:48px;background:radial-gradient(circle at 50% 45%,#d7a688 0%,#7b5646 65%,#3d2a22 100%)" role="img" aria-label="Portrait of a customer"></div>
  <div class="abs avatar" style="left:531px;top:1491px;width:134px;height:134px;background:linear-gradient(180deg,#f6caa4 0%,#efbb92 62%,#2c3446 63%,#222a3a 100%)" role="img" aria-label="Portrait of the featured reviewer"></div>
  <span class="abs" style="left:371px;top:1604px;width:14px;height:14px;border-radius:50%;background:#ef1c2c"></span>
  <span class="abs" style="left:886px;top:1568px;width:7px;height:7px;border-radius:50%;background:#3a7de0"></span>

  <div class="abs reviewer" style="top:1648px;font-weight:500;font-size:20px;color:var(--ink)">Dorian Velasco</div>
  <div class="abs reviewer" style="top:1682px;font-size:12px;color:#555">United States</div>
  <div class="abs reviewer" style="top:1704px;font-size:30px;color:var(--gold);letter-spacing:1px">★★★★★</div>

  <svg class="abs" style="left:160px;top:1669px" width="94" height="81" viewBox="0 0 94 81"><path fill="#dcdcdc" d="M0 81V44C0 18 12 4 36 0l4 11C28 15 22 24 21 37h21v44zm52 0V44C52 18 64 4 88 0l4 11C80 15 74 24 73 37h21v44z"/></svg>
  <svg class="abs" style="left:950px;top:1772px" width="94" height="81" viewBox="0 0 94 81"><g transform="rotate(180 47 40.5)"><path fill="#dcdcdc" d="M0 81V44C0 18 12 4 36 0l4 11C28 15 22 24 21 37h21v44zm52 0V44C52 18 64 4 88 0l4 11C80 15 74 24 73 37h21v44z"/></g></svg>

  <p class="abs quote-text">Itaque earum rerum hic tenetur a sapiente delectus, ut aut reiciendis voluptatibus maiores alias. Consequatur aut perferendis doloribus asperiores repellat.Et harum quidem rerum facilis est et expedita distinctio.</p>
  <div class="abs dots"><i></i><i></i><i></i><i class="on"></i><i></i><i></i></div>
</section>

<footer>
  <div class="abs footer"></div>
  <div class="abs foot-brand"><span>NOVABOND</span><span class="dot"></span></div>
  <span class="abs social" style="left:111px" aria-label="Social profile"></span>
  <span class="abs social" style="left:169px" aria-label="Social profile"></span>
  <span class="abs social" style="left:226px" aria-label="Social profile"></span>
  <span class="abs social" style="left:284px" aria-label="Social profile"></span>

  <div class="abs col quick" style="left:431px;top:1981px">
    <h4>Quick Links</h4>
    <ul>
      <li><svg width="13" height="12" viewBox="0 0 24 22"><path fill="#fff" d="M0 8h12V0l12 11-12 11v-8H0z"/></svg>Home</li>
      <li><svg width="13" height="12" viewBox="0 0 24 22"><path fill="#fff" d="M0 8h12V0l12 11-12 11v-8H0z"/></svg>About</li>
      <li><svg width="13" height="12" viewBox="0 0 24 22"><path fill="#fff" d="M0 8h12V0l12 11-12 11v-8H0z"/></svg>Product</li>
      <li><svg width="13" height="12" viewBox="0 0 24 22"><path fill="#fff" d="M0 8h12V0l12 11-12 11v-8H0z"/></svg>Testimonials</li>
      <li><svg width="13" height="12" viewBox="0 0 24 22"><path fill="#fff" d="M0 8h12V0l12 11-12 11v-8H0z"/></svg>Contact Us</li>
    </ul>
  </div>

  <div class="abs col" style="left:662px;top:1981px">
    <h4>Help Links</h4>
    <ul>
      <li><svg width="13" height="12" viewBox="0 0 24 22"><path fill="#fff" d="M0 8h12V0l12 11-12 11v-8H0z"/></svg>FAQ</li>
      <li><svg width="13" height="12" viewBox="0 0 24 22"><path fill="#fff" d="M0 8h12V0l12 11-12 11v-8H0z"/></svg>Terms of use</li>
      <li><svg width="13" height="12" viewBox="0 0 24 22"><path fill="#fff" d="M0 8h12V0l12 11-12 11v-8H0z"/></svg>Privacy Policy</li>
      <li><svg width="13" height="12" viewBox="0 0 24 22"><path fill="#fff" d="M0 8h12V0l12 11-12 11v-8H0z"/></svg>Support Links</li>
      <li><svg width="13" height="12" viewBox="0 0 24 22"><path fill="#fff" d="M0 8h12V0l12 11-12 11v-8H0z"/></svg>Conditions</li>
    </ul>
  </div>

  <div class="abs col" style="left:880px;top:1981px">
    <h4>Contact Us</h4>
  </div>
  <div class="abs ct" style="left:880px;top:2036px">
    <span class="ic"><svg width="14" height="18" viewBox="0 0 24 32"><path fill="#000" d="M12 0a12 12 0 0 0-12 12c0 9 12 20 12 20s12-11 12-20A12 12 0 0 0 12 0zm0 17a5 5 0 1 1 0-10 5 5 0 0 1 0 10z"/></svg></span>
    <span>Novabond<br>United States</span>
  </div>
  <div class="abs ct" style="left:880px;top:2093px">
    <span class="ic"><svg width="15" height="15" viewBox="0 0 24 24"><path fill="#000" d="M6.6 10.8a15.1 15.1 0 0 0 6.6 6.6l2.2-2.2c.3-.3.7-.4 1-.2 1.1.4 2.3.6 3.6.6.6 0 1 .4 1 1V20c0 .6-.4 1-1 1A17 17 0 0 1 3 4c0-.6.4-1 1-1h3.5c.6 0 1 .4 1 1 0 1.3.2 2.5.6 3.6.1.3 0 .7-.2 1z"/></svg></span>
    <span>+1 555 014 2387</span>
  </div>
  <div class="abs ct" style="left:880px;top:2145px">
    <span class="ic"><svg width="15" height="11" viewBox="0 0 24 18"><rect width="24" height="18" rx="2" fill="#000"/><path d="M2 3l10 7 10-7" stroke="#fff" stroke-width="2" fill="none"/></svg></span>
    <span>info@novabond.example</span>
  </div>

  <div class="abs rule"></div>
  <p class="abs copy">Copyrights@2023.Novabond.All Rights Reserved</p>
</footer>

</body>
</html>
```